RevelHubQZ Business Cards

Front
Has logo with a design. Website address (www.revelhubqz-example.net)
Has slogan (discover the nightlife)
Has phone number (5182297734)
Should be bold and stands out.

Back
Has details about what we offer.

Events
Search upcoming events
Submit events
Party Image Gallery
View and download HQ party images
Sign up as a contributing event photographer and get paid!
Tickets
Sell your event tickets online for free!
Direct pay
No ticket fee

Target Market(s)

These cards will be handed out in clubs and events to patrons.

Industry/Entity Type

Business

Contact Information for Business Card

Should match or mirror our website in some sort of way. Visit the website to get ideas.

Requirements
Must have
• Must be designed for a 3x3 inch card.

```html
<!DOCTYPE html>
<html lang="en">
<head>
<meta charset="utf-8">
<title>RevelHubQZ Business Cards</title>
<link href="https://fonts.googleapis.com/css2?family=Arimo:wght@400;700&display=swap" rel="stylesheet">
<style>
  :root {
    --page: #e9e7e4;
    --card: #141414;
    --card-edge: #1d1d1d;
    --cyan: #2aa9e0;
    --pink: #e5338c;
    --ink: #f2f2f2;
    --muted: #8a8a8a;
  }
  * { box-sizing: border-box; margin: 0; padding: 0; }
  html, body { width: 1200px; height: 1200px; overflow: hidden; }
  body {
    background: var(--page);
    font-family: "Arimo", Arial, sans-serif;
    color: var(--ink);
    position: relative;
  }
  .card {
    position: absolute;
    left: 150px;
    width: 900px;
    height: 515px;
    background: linear-gradient(160deg, var(--card-edge), var(--card));
    border-radius: 28px;
    box-shadow: 0 14px 30px rgba(0,0,0,.28);
    overflow: hidden;
  }
  .card--back { top: 60px; }
  .card--front { top: 625px; }

  .brand { position: absolute; display: flex; align-items: center; gap: 16px; }
  .brand__dot { width: 34px; height: 34px; border-radius: 50%; background: var(--cyan); flex: none; }
  .brand__name { font-size: 56px; font-weight: 400; color: var(--cyan); letter-spacing: .5px; line-height: 1; }
  .brand__slogan {
    position: absolute; font-size: 15px; letter-spacing: 6px;
    color: var(--muted); text-transform: lowercase;
  }

  .card--back .brand { top: 78px; left: 270px; }
  .card--back .brand__slogan { top: 146px; left: 320px; }

  .feature-list { position: absolute; list-style: none; font-size: 21px; line-height: 1; }
  .feature-list li { display: flex; align-items: center; gap: 12px; margin-bottom: 20px; }
  .feature-list--short { top: 110px; left: 70px; }
  .feature-list--long { top: 250px; right: 70px; text-align: right; }
  .feature-list--long li { justify-content: flex-end; }
  .bullet {
    width: 14px; height: 14px; flex: none;
    background:
      linear-gradient(var(--cyan), var(--cyan)) 0 0 / 6px 6px no-repeat,
      linear-gradient(var(--cyan), var(--cyan)) 8px 0 / 6px 6px no-repeat,
      linear-gradient(var(--cyan), var(--cyan)) 0 8px / 6px 6px no-repeat,
      linear-gradient(var(--cyan), var(--cyan)) 8px 8px / 6px 6px no-repeat;
  }

  .card--front .brand { top: 90px; left: 70px; }
  .card--front .brand__slogan { top: 158px; left: 120px; }
  .divider {
    position: absolute; left: 520px; top: 60px;
    width: 3px; height: 395px; background: var(--cyan);
  }
  .contact { position: absolute; left: 550px; bottom: 80px; font-size: 24px; line-height: 1.5; }
</style>
</head>
<body>

  <section class="card card--back" aria-label="Card back">
    <div class="brand">
      <span class="brand__dot"></span>
      <span class="brand__name">RevelHubQZ</span>
    </div>
    <p class="brand__slogan">discover the nightlife</p>

    <ul class="feature-list feature-list--short">
      <li><span class="bullet"></span>Events</li>
      <li><span class="bullet"></span>Tickets</li>
      <li><span class="bullet"></span>Direct pay</li>
      <li><span class="bullet"></span>No ticket fee</li>
      <li><span class="bullet"></span>Submit events</li>
    </ul>

    <ul class="feature-list feature-list--long">
      <li>Search upcoming events<span class="bullet"></span></li>
      <li>Party Image Gallery<span class="bullet"></span></li>
      <li>View and download HQ party images<span class="bullet"></span></li>
      <li>Sell your event tickets online for free!<span class="bullet"></span></li>
      <li>Sign up as a contributing event photographer and get paid!<span class="bullet"></span></li>
    </ul>
  </section>

  <section class="card card--front" aria-label="Card front">
    <div class="brand">
      <span class="brand__dot"></span>
      <span class="brand__name">RevelHubQZ</span>
    </div>
    <p class="brand__slogan">discover the nightlife</p>
    <span class="divider"></span>
    <div class="contact">
      <p>Tel: 5182297734</p>
      <p>Web: www.revelhubqz-example.net</p>
    </div>
  </section>

</body>
</html>
```